BRIGHT RIVER POWER.

I'd like my business logo.
contact name: Dennis Halvorsen
phone:0438759164
email: info@brightriverpower.net.au
website: www.brightriverpower.net.au

services:
solar
battery storage
LED lighting
energy saving solutions
general electrical
I'd like the design to look professional

Target Market(s)

Everyone

Industry/Entity Type

Business

Contact Information for Business Card

as described above

Requirements
Must have
• Id like the colours and the design to work well with my logo.

```html
<!DOCTYPE html>
<html lang="en">
<head>
<meta charset="UTF-8">
<title>Bright River Power – Business Card</title>
<link rel="stylesheet" href="https://fonts.googleapis.com/css2?family=Open+Sans:wght@600;700&display=swap">
<style>
  :root {
    --page-bg: #ececea;
    --card-white: #ffffff;
    --brand-green: #62ad35;
    --brand-green-light: #9fcf3f;
    --brand-orange: #f8a814;
    --brand-orange-soft: #fbc85a;
    --text-light: #ffffff;
    --logo-green: #5aa534;
  }
  * { margin: 0; padding: 0; box-sizing: border-box; }
  html, body {
    width: 1200px;
    height: 900px;
    overflow: hidden;
    background: var(--page-bg);
    font-family: "Open Sans", Arial, sans-serif;
  }
  .card {
    position: absolute;
    left: 100px;
    top: 140px;
    width: 1000px;
    height: 620px;
    background: var(--card-white);
    overflow: hidden;
    box-shadow: 0 10px 30px rgba(0,0,0,0.12);
  }
  .band-contact {
    position: absolute;
    left: 0; top: 229px;
    width: 100%; height: 258px;
    background: var(--brand-green);
  }
  .band-services {
    position: absolute;
    left: 0; top: 487px;
    width: 100%; height: 133px;
    background: var(--brand-orange);
  }
  .brand-mark {
    position: absolute;
    left: 55px; top: 78px;
    display: flex;
    align-items: center;
    gap: 16px;
  }
  .brand-dot {
    width: 44px; height: 44px;
    border-radius: 50%;
    background: var(--brand-orange);
  }
  .brand-name {
    font-size: 34px;
    font-weight: 700;
    color: var(--logo-green);
    letter-spacing: 0.5px;
  }
  .symbol-area {
    position: absolute;
    left: 590px; top: 20px;
    width: 410px; height: 600px;
    border-radius: 205px 0 0 205px;
    background: radial-gradient(circle at 65% 45%, var(--brand-green-light) 0%, var(--brand-green) 45%, var(--brand-orange-soft) 78%, rgba(255,255,255,0) 100%);
    opacity: 0.9;
  }
  .contact-name {
    position: absolute;
    left: 72px; top: 277px;
    font-size: 36px;
    font-weight: 700;
    color: var(--text-light);
  }
  .contact-list {
    position: absolute;
    left: 72px; top: 348px;
    list-style: none;
    color: var(--text-light);
    font-size: 25px;
    font-weight: 600;
  }
  .contact-list li {
    display: flex;
    align-items: center;
    gap: 14px;
    height: 36px;
  }
  .contact-list svg { width: 20px; height: 20px; fill: var(--text-light); flex: none; }
  .services {
    position: absolute;
    left: 72px; top: 505px;
    color: var(--text-light);
    font-size: 26px;
    font-weight: 700;
    line-height: 36px;
  }
  .services .sep {
    display: inline-block;
    width: 12px; height: 12px;
    border-radius: 50%;
    background: var(--text-light);
    margin: 0 6px 3px 14px;
    vertical-align: middle;
  }
</style>
</head>
<body>
  <article class="card">
    <div class="band-contact"></div>
    <div class="band-services"></div>

    <div class="brand-mark">
      <span class="brand-dot"></span>
      <span class="brand-name">BRIGHT RIVER POWER</span>
    </div>

    <div class="symbol-area" role="img" aria-label="Large brand symbol decoration: sun rays over a light bulb with leaves"></div>

    <h1 class="contact-name">Dennis Halvorsen</h1>
    <ul class="contact-list">
      <li>
        <svg viewBox="0 0 24 24" aria-hidden="true"><path d="M6.6 10.8a15.1 15.1 0 0 0 6.6 6.6l2.2-2.2a1 1 0 0 1 1-.25 11.4 11.4 0 0 0 3.6.57 1 1 0 0 1 1 1V20a1 1 0 0 1-1 1A17 17 0 0 1 3 4a1 1 0 0 1 1-1h3.5a1 1 0 0 1 1 1c0 1.25.2 2.45.57 3.57a1 1 0 0 1-.25 1z"/></svg>
        0438759164
      </li>
      <li>
        <svg viewBox="0 0 24 24" aria-hidden="true"><path d="M3 5h18v14H3z M3 5l9 7 9-7" fill="none" stroke="#fff" stroke-width="2"/></svg>
        info@brightriverpower.net.au
      </li>
      <li>
        <svg viewBox="0 0 24 24" aria-hidden="true"><circle cx="12" cy="12" r="9" fill="none" stroke="#fff" stroke-width="2"/><path d="M3 12h18M12 3c3 3 3 15 0 18M12 3c-3 3-3 15 0 18" fill="none" stroke="#fff" stroke-width="1.6"/></svg>
        www.brightriverpower.net.au
      </li>
    </ul>

    <p class="services">
      Solar<span class="sep"></span>Battery Storage<span class="sep"></span>LED Lighting<br>
      Energy Saving Solutions
    </p>
  </article>
</body>
</html>
```